Modern Business Card for Larkwell 2018

Our company assumes the best about people. We are creating an online community of entrepreneurs and business leaders who struggle with marketing their business online.

This business card should POP! We recently got a new logo and are launching a new website next month, so our business cards should make a statement that feels:
-Fresh
-Smart
-Trustworthy
-Fun

Target Market(s)

small business owners, entrepreneurs

Industry/Entity Type

Digital Marketing

Contact Information for Business Card

Dimensions: 3.5" x 2"

Font styles to use
Sans Serif

Colors
f37122
ffffff

Requirements
Must have
• We need a business card with a modern, bold design. We will use one side of the card as a lead-generation offer, so text on one side will need to fit up to 140 characters. The business card should stick to our core colors (orange, black, and white).
Nice to have
• We think a vertical "portrait" design could be interesting.
Should not have
• Should not look like a traditional business card. The round icon should stand out from a distance.

```html
<!DOCTYPE html>
<html lang="en">
<head>
<meta charset="utf-8">
<title>Larkwell Business Card</title>
<link href="https://fonts.googleapis.com/css2?family=Montserrat:wght@700&family=Roboto:wght@400;500;700&family=Lobster&family=Permanent+Marker&display=swap" rel="stylesheet">
<style>
  :root {
    --brand-orange: #f37122;
    --card-white: #f3f3f3;
    --ink: #222222;
    --paper: #ffffff;
    --backdrop: #6e4a33;
  }
  * { margin: 0; padding: 0; box-sizing: border-box; }
  html, body { width: 1200px; height: 960px; overflow: hidden; }
  body { background: var(--backdrop); position: relative; font-family: "Roboto", sans-serif; }

  .card { position: absolute; width: 600px; height: 342px; border-radius: 18px; overflow: hidden; }
  .card-front { left: 314px; top: 113px; background: var(--card-white); }
  .card-back { left: 311px; top: 472px; background: var(--brand-orange); color: var(--paper); }

  .brand-dot { position: absolute; border-radius: 50%; width: 44px; height: 44px; }
  .card-front .brand-dot { left: 144px; top: 35px; background: var(--brand-orange); }
  .brand-name {
    position: absolute; left: 38px; top: 92px;
    font-family: "Montserrat", sans-serif; font-weight: 700; font-size: 41px;
    letter-spacing: 0.5px; color: var(--ink); line-height: 1; white-space: nowrap;
  }
  .brand-tagline {
    position: absolute; left: 40px; top: 137px;
    font-family: "Permanent Marker", cursive; font-size: 12.5px;
    letter-spacing: 0.8px; color: var(--ink); text-transform: uppercase; white-space: nowrap;
  }

  .name-band { position: absolute; left: 279px; top: 179px; width: 321px; height: 136px; }
  .contact { position: absolute; right: 24px; top: 200px; text-align: right; color: var(--paper); white-space: nowrap; }
  .contact-name { font-family: "Lobster", cursive; font-size: 32px; line-height: 1.05; letter-spacing: 0; text-transform: uppercase; }
  .contact-role { font-size: 17.5px; margin-top: 12px; letter-spacing: 0.4px; line-height: 1.1; }
  .contact-email { font-size: 14.5px; margin-top: 5px; letter-spacing: 3px; line-height: 1.1; }

  .card-back .brand-dot { left: 271px; top: 22px; background: var(--paper); }
  .offer { position: absolute; left: 0; right: 0; top: 75px; text-align: center; white-space: nowrap; }
  .offer-headline { font-weight: 700; font-size: 19.5px; line-height: 21px; text-transform: uppercase; letter-spacing: 0.2px; }
  .offer-copy { font-size: 16px; line-height: 19px; margin-top: 9px; }
  .offer-url { font-weight: 700; font-size: 21px; line-height: 23px; }

  .notes-box { position: absolute; left: 20px; top: 224px; width: 557px; height: 101px; background: var(--paper); border-radius: 16px; }
  .notes-line { position: absolute; left: 24px; right: 27px; height: 1px; background: var(--ink); }
  .notes-line.first { top: 31px; }
  .notes-line.second { top: 71px; }
</style>
</head>
<body>
  <section class="card card-front">
    <span class="brand-dot"></span>
    <div class="brand-name">LARKWELL</div>
    <div class="brand-tagline">Tell stories that inspire action</div>
    <svg class="name-band" viewBox="0 0 321 136" aria-hidden="true">
      <polygon points="31,0 321,0 321,136 0,136" fill="var(--brand-orange)"/>
    </svg>
    <div class="contact">
      <div class="contact-name">Dana Whitlow</div>
      <div class="contact-role">STORY MARKETING COACH</div>
      <div class="contact-email">dana@larkwellnow.com</div>
    </div>
  </section>

  <section class="card card-back">
    <span class="brand-dot"></span>
    <div class="offer">
      <div class="offer-headline">Reach more people.<br>Make more money.<br>Create more impact.</div>
      <div class="offer-copy">Get your free Larkwell, Starter Package and our<br>marketing guide today at</div>
      <div class="offer-url">Larkwellnow.com/start</div>
    </div>
    <div class="notes-box">
      <span class="notes-line first"></span>
      <span class="notes-line second"></span>
    </div>
  </section>
</body>
</html>
```